Design for schnapps bottle label "Río Ámbar"

Hi! On a small land lot we are producing our own Italian schnapps "Grappa". For the bottles we would like to modernize our current labes that you find below. The two cats looking at each other should remain, but updated and more modern. I am very much looking forward to your suggestions. Best, Jens

Target Market(s)

Schnapps bottle label

Requirements
Must have
• Cats should resemble the cats that are decorating the house entry (see attached), however, should have a more modern appearance.

Text elements should remain: "Grappa", "Río Ámbar", "Legnoso", "[Vintage Year], "Raccolta No", "Vol %"
Should not have
• Current ornament can be used, replaced or deleted (whatever looks best)

```html
<!DOCTYPE html>
<html lang="it">
<head>
<meta charset="utf-8">
<title>Grappa di Río Ámbar – Legnoso 2015</title>
<link rel="stylesheet" href="https://fonts.googleapis.com/css2?family=Cormorant+Garamond:wght@400;500&family=Allura&display=swap">
<style>
  :root {
    --backdrop: #e4e4e4;
    --label-black: #0d0d0d;
    --gold: #d6a838;
    --gold-light: #f0cd63;
    --gold-deep: #a9761d;
    --ink: #1a1408;
  }
  * { box-sizing: border-box; margin: 0; padding: 0; }
  html, body {
    width: 838px;
    height: 1200px;
    overflow: hidden;
    background: var(--backdrop);
  }
  .label {
    position: absolute;
    left: 119px;
    top: 115px;
    width: 600px;
    height: 970px;
    background: var(--label-black);
    color: var(--gold);
    font-family: "Cormorant Garamond", serif;
    text-align: center;
  }
  .label__title {
    position: absolute;
    top: 92px;
    width: 100%;
    font-size: 74px;
    font-weight: 500;
    letter-spacing: 3px;
    line-height: 1;
  }
  .label__di {
    position: absolute;
    top: 208px;
    width: 100%;
    font-size: 20px;
    letter-spacing: 2px;
  }
  .label__brand {
    position: absolute;
    top: 272px;
    width: 100%;
    font-family: "Allura", cursive;
    font-size: 92px;
    line-height: 1;
  }
  .label__style {
    position: absolute;
    top: 474px;
    width: 100%;
    font-size: 28px;
    letter-spacing: 2px;
    line-height: 1.2;
    z-index: 2;
  }
  .label__cats {
    position: absolute;
    left: 0;
    top: 560px;
    width: 100%;
    height: 243px;
    background: linear-gradient(100deg, var(--gold-deep), var(--gold-light) 45%, var(--gold) 70%, var(--gold-deep));
  }
  .label__band {
    position: absolute;
    left: 0;
    bottom: 0;
    width: 100%;
    height: 167px;
    background: linear-gradient(100deg, var(--gold-deep), var(--gold-light) 40%, var(--gold) 65%, var(--gold-deep));
    color: var(--ink);
    font-size: 27px;
    line-height: 1.55;
    padding-top: 36px;
    letter-spacing: 0.5px;
  }
</style>
</head>
<body>
  <main class="label">
    <h1 class="label__title">GRAPPA</h1>
    <p class="label__di">DI</p>
    <p class="label__brand">Río Ámbar</p>
    <p class="label__style">LEGNOSO<br>2015</p>
    <div class="label__cats" role="img" aria-label="Two stylised gold cats stretching towards each other, noses touching, tails curled upward"></div>
    <div class="label__band">
      <p>RACCOLTA NO.01</p>
      <p>41.0% VOL. 70 CL</p>
    </div>
  </main>
</body>
</html>
```